Modern Business Card

Modern professional business card with more than just logo and demographic info. Something memorable.

We are a trendy/modern chiropractic group with an emphasis on neurology, hence the minimalist-type brain logo. We want to convey that modern and technical aspect with professionalism and the elite nature of our practice environment.

```html
<!DOCTYPE html>
<html lang="en">
<head>
<meta charset="UTF-8">
<title>Meridian Spine – Business Card</title>
<link rel="stylesheet" href="https://fonts.googleapis.com/css2?family=Roboto:wght@400;500&display=swap">
<style>
  :root {
    --page-bg: #f3f3f3;
    --card-white: #fdfdfd;
    --card-dark: #222324;
    --brand-blue: #4a7fc1;
    --ink-dark: #1f1f1f;
    --ink-grey: #707070;
    --band-dark: #232323;
    --back-mark: #4a4b4d;
  }
  * { box-sizing: border-box; margin: 0; padding: 0; }
  html, body {
    width: 1200px; height: 1200px; overflow: hidden;
    background: var(--page-bg);
    font-family: "Roboto", Arial, sans-serif;
  }
  .canvas { position: relative; width: 1200px; height: 1200px; }

  /* Front card */
  .card-front {
    position: absolute; left: 232px; top: 173px;
    width: 705px; height: 409px;
    background: var(--card-white);
    overflow: hidden;
    border: 1px solid #e4e4e4;
  }
  .brand {
    position: absolute; left: 48px; top: 162px;
    display: flex; align-items: center; gap: 16px;
  }
  .brand-square {
    width: 60px; height: 60px; background: var(--brand-blue);
  }
  .brand-name {
    font-size: 38px; font-weight: 500; line-height: 1.0;
    color: var(--ink-dark); letter-spacing: 1px;
    text-transform: uppercase;
  }
  .divider {
    position: absolute; left: 385px; top: 89px;
    width: 2px; height: 231px; background: var(--brand-blue);
  }
  .person { position: absolute; left: 420px; top: 82px; }
  .person-name {
    font-size: 33px; font-weight: 400; color: var(--brand-blue); line-height: 1.1;
  }
  .person-role {
    font-size: 21px; color: var(--ink-grey); margin-top: 4px;
  }
  .address {
    position: absolute; left: 413px; top: 165px;
    font-size: 19px; line-height: 24px; color: var(--ink-grey);
  }
  .contact-list {
    position: absolute; left: 413px; top: 221px; list-style: none;
  }
  .contact-item {
    display: flex; align-items: center; gap: 15px;
    height: 26px; font-size: 19px; color: var(--ink-grey);
  }
  .contact-item svg { width: 19px; height: 19px; fill: var(--brand-blue); flex: none; }
  .footer-band { position: absolute; left: 0; bottom: 0; width: 705px; height: 18px; }

  /* Back card */
  .card-back {
    position: absolute; left: 231px; top: 628px;
    width: 702px; height: 401px;
    background: var(--card-dark);
    display: flex; align-items: center; justify-content: center;
  }
  .back-brand {
    display: flex; align-items: center; gap: 18px;
  }
  .back-brand .brand-square { width: 70px; height: 70px; background: var(--back-mark); }
  .back-brand .brand-name { color: var(--back-mark); font-size: 46px; }
</style>
</head>
<body>
<main class="canvas">

  <section class="card-front" aria-label="Business card front">
    <div class="brand">
      <span class="brand-square"></span>
      <span class="brand-name">Meridian<br>Spine</span>
    </div>

    <div class="divider"></div>

    <div class="person">
      <p class="person-name">Calder Voss</p>
      <p class="person-role">President</p>
    </div>

    <p class="address">012 Physical Address 000<br>United State 5551</p>

    <ul class="contact-list">
      <li class="contact-item">
        <svg viewBox="0 0 24 24" aria-hidden="true"><path d="M6.6 10.8a15.1 15.1 0 0 0 6.6 6.6l2.2-2.2a1 1 0 0 1 1-.25 11.4 11.4 0 0 0 3.6.57 1 1 0 0 1 1 1V20a1 1 0 0 1-1 1A17 17 0 0 1 3 4a1 1 0 0 1 1-1h3.5a1 1 0 0 1 1 1c0 1.25.2 2.45.57 3.57a1 1 0 0 1-.25 1z"/></svg>
        012 3456 7890
      </li>
      <li class="contact-item">
        <svg viewBox="0 0 24 24" aria-hidden="true"><path d="M6 2h12v5H6zM4 8h16a2 2 0 0 1 2 2v7h-4v5H6v-5H2v-7a2 2 0 0 1 2-2zm4 8v4h8v-4z"/></svg>
        00000000051
      </li>
      <li class="contact-item">
        <svg viewBox="0 0 24 24" aria-hidden="true"><path d="M2 4h18v8.5a5.5 5.5 0 0 0-7.4 6.5H2zm2 2 7 5 7-5v-.1H4zM18 14a4 4 0 1 1 0 8 4 4 0 0 1 0-8zm-1 5.2-1.3-1.3-.8.8 2.1 2.1 3.3-3.3-.8-.8z"/></svg>
        info@yourmail.com
      </li>
      <li class="contact-item">
        <svg viewBox="0 0 24 24" aria-hidden="true"><path d="M12 2a10 10 0 1 0 0 20 10 10 0 0 0 0-20zm0 1.6c1 0 2.3 2 2.7 5.4H9.3C9.7 5.6 11 3.6 12 3.6zm-2.9.6A13 13 0 0 0 7.7 9H4.1a8.4 8.4 0 0 1 5-4.8zm5.8 0A8.4 8.4 0 0 1 19.9 9h-3.6a13 13 0 0 0-1.4-4.8zM3.7 10.6h3.9a19 19 0 0 0 0 2.8H3.7a8.4 8.4 0 0 1 0-2.8zm5.5 0h5.6a17 17 0 0 1 0 2.8H9.2a17 17 0 0 1 0-2.8zm7.2 0h3.9a8.4 8.4 0 0 1 0 2.8h-3.9a19 19 0 0 0 0-2.8zM4.1 15h3.6a13 13 0 0 0 1.4 4.8A8.4 8.4 0 0 1 4.1 15zm5.2 0h5.4c-.4 3.4-1.7 5.4-2.7 5.4S9.7 18.4 9.3 15zm7 0h3.6a8.4 8.4 0 0 1-5 4.8 13 13 0 0 0 1.4-4.8z"/></svg>
        www.yourwebside.com
      </li>
    </ul>

    <svg class="footer-band" viewBox="0 0 705 18" aria-hidden="true">
      <polygon points="0,0 361,0 356,18 0,18" fill="var(--band-dark)"/>
      <polygon points="367,0 705,0 705,18 362,18" fill="var(--brand-blue)"/>
    </svg>
  </section>

  <section class="card-back" aria-label="Business card back">
    <div class="back-brand">
      <span class="brand-square"></span>
      <span class="brand-name">Meridian<br>Spine</span>
    </div>
  </section>

</main>
</body>
</html>
```